Vorelan.com Personal Trainer/Fitness Website

I want a website to market my personal training/Outdoor Bootcamp Class services, as well as to ditribute nutrivex. I need a logo as well I included an address for the Harbor Gales 1975 logo. I'd like Vorelan in place of Harbor Gales, and in Black and white, just different enough so I can't get sued by the PBL.
https://www.pictofind.example/imgres?imgurl=http%3A%2F%2Fwww.darnell-quibury.example%2Fwp-content%2Fuploads%2F2014%2F01%2Fgales_logo4.jpg&imgrefurl=http%3A%2F%2Fwww.darnell-quibury.example%2Fpbl-logo-redesigns-harbor-gales%2F&docid=_qkwzR7TBAgXpL&tbnid=m4tpU8KdOXjnRP%3A&w=600&h=450&client=ms-android-carrier&bih=512&biw=360&ved=0ahUKEwiRtpgyp9HMAhUTwGMKHRPMBWMQMwg6KBQwFA&iact=mrc&uact=8.
It should be about 5 pages 1. home 2. about 3. Services 4. Blog/Videos and programs 5. Contact.
http://www.dorvinfitness.example.uk/ is a website I like the style of.

Target Market(s)

Seattle area

Industry/Entity Type

Fitness

Coding

Coded - Design and coding required

Number of Pages Required

4 page

Font styles to use
Serif
Sans Serif

Requirements
Must have
• A minimal look
Nice to have
• A logo similar to the 1975 Harbor Galewinds Logo, with a Small Milo Brandt ripping his shirt open(with a picture of the logo on his shirt, picture within picture) to turn into Ironjaw in the center. Skyline is black, Background and small figure white(with black logo on shirt)

```html
<!DOCTYPE html>
<html lang="en">
<head>
<meta charset="utf-8">
<title>Vorelan – Personal Training</title>
<link href="https://fonts.googleapis.com/css2?family=Lato:wght@400;700&family=Raleway:wght@300;400&family=Questrial&display=swap" rel="stylesheet">
<style>
:root{
  --green:#0b6a3a;
  --green-dark:#08552f;
  --red:#e2282c;
  --black:#000;
  --ink:#222;
  --dark:#2b2a2a;
  --white:#fff;
  --grey:#8a8a8a;
}
*{box-sizing:border-box;margin:0;padding:0}
html,body{width:1200px;height:2406px;overflow:hidden}
body{position:relative;font-family:'Lato',sans-serif;color:var(--ink);background:var(--white)}
.abs{position:absolute}
a{color:inherit}

/* header */
.topbar{left:0;top:0;width:1200px;height:115px;background:var(--black)}
.contact-line{left:132px;color:var(--white);font-size:18px;display:flex;align-items:center;gap:14px}
.contact-line svg{width:28px;height:28px}
.social{right:130px;top:14px;display:flex;gap:10px}
.social span{width:16px;height:16px;border-radius:50%;background:var(--red);display:block}
.trainer-btn{left:823px;top:56px;width:244px;height:45px;background:#555;border-radius:4px;display:flex;align-items:center;color:var(--white);font-size:21px;letter-spacing:.5px}
.trainer-btn .cap{width:62px;height:45px;background:var(--green);border-radius:4px 0 0 4px;display:flex;align-items:center;justify-content:center;margin-right:14px}
.brand{left:510px;top:8px;width:174px;height:160px;background:var(--white);border-radius:87px 87px 0 0;display:flex;flex-direction:column;align-items:center}
.brand-mark{margin-top:16px;width:88px;height:88px;border-radius:50%;border:6px solid var(--green)}
.brand-name{font-family:'Lato',sans-serif;font-weight:700;font-size:38px;color:var(--green);margin-top:2px;letter-spacing:1px}
.nav{left:0;top:115px;width:1200px;height:45px;background:var(--white)}
.nav a{position:absolute;top:0;height:45px;line-height:45px;text-decoration:none;font-size:17px;color:#111}
.nav a.active{background:var(--green);color:var(--white);text-align:center;width:110px;left:103px}

/* hero */
.hero{left:0;top:160px;width:1200px;height:397px;background:linear-gradient(180deg,#cfcac4 0%,#b9b1a6 55%,#8a6a44 100%)}
.hero-arrow{top:180px;width:40px;height:40px;border:2px solid var(--white);border-radius:50%}
.hero-title{left:0;top:500px;width:1200px;text-align:center;font-family:'Questrial',sans-serif;font-weight:700;font-size:30px;color:var(--white);letter-spacing:1px;-webkit-text-stroke:.6px var(--white)}

/* sections */
.services{left:0;top:557px;width:1200px;height:511px;background:radial-gradient(ellipse at 50% 45%,#1b7a4a 0%,var(--green) 45%,var(--green-dark) 100%)}
.sec-title{width:1200px;left:0;text-align:center;font-family:'Raleway',sans-serif;font-weight:400;font-size:33px;letter-spacing:1px}
.rule{height:1px;left:145px;width:910px}
.accent{height:3px;width:78px;left:561px;background:var(--red)}
.intro{left:190px;top:668px;width:820px;text-align:center;color:var(--white);font-size:15.5px;line-height:26px}
.svc{width:260px;text-align:center;color:var(--white)}
.svc .icon{width:118px;height:118px;border-radius:50%;background:var(--black);border:3px solid var(--white);margin:0 auto}
.svc h3{font-size:23px;font-weight:700;margin-top:26px}
.svc p{font-size:15.5px;line-height:22px;margin-top:8px}
.svc a{display:inline-block;margin-top:18px;font-size:14px;font-weight:700;text-decoration:underline}

.about{left:0;top:1068px;width:1200px;height:441px;background:var(--dark)}
.about-photo-bg{left:640px;top:1068px;width:560px;height:441px;background:linear-gradient(135deg,#2f3b2a 0%,#4e5b36 50%,#6c6a42 100%);clip-path:polygon(28% 0,100% 0,100% 100%,0 100%)}
.about-title{left:135px;top:1094px;font-family:'Raleway',sans-serif;font-weight:400;font-size:34px;color:var(--white)}
.portrait{left:132px;top:1200px;width:248px;height:244px;background:linear-gradient(160deg,#9cb4c4,#4e5f6c)}
.about-head{left:425px;top:1214px;font-family:'Raleway',sans-serif;font-size:29px;color:var(--white)}
.about-head em{font-style:normal;color:var(--red)}
.about-text{left:425px;top:1262px;width:540px;font-size:14px;line-height:19.7px;color:var(--white)}

.reviews-title{color:var(--green);top:1554px}
.quote{left:131px;top:1642px;width:75px;height:75px;border-radius:50%;background:var(--green)}
.review{left:223px;top:1632px;width:845px;font-size:13.5px;line-height:22.5px;color:#333}
.stars{left:222px;top:1754px;display:flex;gap:6px}
.reviewer{left:223px;top:1782px;font-family:Arial,sans-serif;font-size:16px;color:var(--green)}
.reviewer b{font-weight:700}

.start{left:0;top:1846px;width:1200px;height:257px;background:var(--black)}
.thanks{left:0;top:1956px;width:1200px;text-align:center;color:var(--white);font-size:23px}
.info{display:flex;align-items:center;gap:16px;color:var(--white);font-size:18px;line-height:26px}
.info .ring{width:40px;height:40px;border:1px solid var(--white);border-radius:50%;display:flex;align-items:center;justify-content:center;flex:none}

.form{left:0;top:2103px;width:1200px;height:257px;background:var(--green)}
.notch{left:584px;top:2103px;width:0;height:0;border-left:16px solid transparent;border-right:16px solid transparent;border-top:16px solid var(--black)}
.form-title{left:0;top:2134px;width:1200px;text-align:center;font-family:'Raleway',sans-serif;font-size:25px;color:var(--white)}
.field{background:var(--white);font-size:14px;color:#333;padding:10px 12px}
.send{left:765px;top:2244px;width:144px;height:37px;background:#111;color:var(--white);font-size:18px;text-align:center;line-height:37px;letter-spacing:1px}

.footer{left:0;top:2360px;width:1200px;height:46px;background:var(--black);color:var(--white);font-size:11.5px}
.footer .copy{position:absolute;left:133px;top:16px}
.footer .social{top:16px;right:130px}
</style>
</head>
<body>

<header>
  <div class="abs topbar"></div>
  <div class="abs contact-line" style="top:18px">
    <svg viewBox="0 0 28 28"><circle cx="14" cy="14" r="12" fill="none" stroke="#e2282c" stroke-width="2"/><path d="M10 8l3 3-2 2c1 2 2 3 4 4l2-2 3 3-2 2c-5 0-10-5-10-10z" fill="#e2282c"/></svg>
    <span>012.555.0147</span>
  </div>
  <div class="abs contact-line" style="top:63px">
    <svg viewBox="0 0 28 28"><circle cx="14" cy="14" r="12" fill="none" stroke="#e2282c" stroke-width="2"/><rect x="8" y="10" width="12" height="9" fill="#e2282c"/><path d="M8 10l6 5 6-5" stroke="#000" stroke-width="1.2" fill="none"/></svg>
    <span>info@vorelan.com</span>
  </div>
  <div class="abs social"><span></span><span></span><span></span><span></span></div>
  <div class="abs trainer-btn">
    <div class="cap"><svg width="30" height="30" viewBox="0 0 30 30"><circle cx="15" cy="15" r="11" fill="#fff"/></svg></div>
    FIND A TRAINER
  </div>
  <nav class="abs nav">
    <a class="active" href="#">HOME</a>
    <a href="#" style="left:239px">ABOUT US</a>
    <a href="#" style="left:377px">SERVICES</a>
    <a href="#" style="left:735px">BLOG</a>
    <a href="#" style="left:836px">PROGRAMS</a>
    <a href="#" style="left:987px">CONTACT</a>
  </nav>
  <div class="abs brand">
    <div class="brand-mark"></div>
    <div class="brand-name">VORELAN</div>
  </div>
</header>

<section>
  <div class="abs hero" role="img" aria-label="Gym interior with exercise balls, squat rack and mirrored wall"></div>
  <div class="abs hero-arrow" style="left:32px"><svg width="36" height="36" viewBox="0 0 36 36"><path d="M21 11l-7 7 7 7" stroke="#fff" stroke-width="2" fill="none"/></svg></div>
  <div class="abs hero-arrow" style="left:1103px"><svg width="36" height="36" viewBox="0 0 36 36"><path d="M15 11l7 7-7 7" stroke="#fff" stroke-width="2" fill="none"/></svg></div>
  <h1 class="abs hero-title">GET FIT &amp; HAVE FUN THE WAY IT SHOULD BE</h1>
</section>

<section>
  <div class="abs services" role="img" aria-label="Faint green-tinted background of an athlete training"></div>
  <h2 class="abs sec-title" style="top:592px;color:#fff">OUR SERVICES</h2>
  <div class="abs rule" style="top:646px;background:rgba(255,255,255,.35)"></div>
  <div class="abs accent" style="top:644px"></div>
  <p class="abs intro">Lorem ipsum dolor sit amet, consectetur adipiscing elit. Morbi quis ante sed massa consectetur feugiat id at tellus. Fusce tristique dictum tincidunt. Nam viverra euismod pretium</p>

  <div class="abs svc" style="left:136px;top:743px">
    <div class="icon"><svg width="112" height="112" viewBox="0 0 112 112"><circle cx="56" cy="42" r="9" fill="#fff"/><rect x="44" y="54" width="24" height="26" rx="6" fill="#fff"/><rect x="28" y="58" width="56" height="5" fill="#fff"/><rect x="24" y="52" width="6" height="16" fill="#fff"/><rect x="82" y="52" width="6" height="16" fill="#fff"/></svg></div>
    <h3>Personal Training</h3>
    <p>Lorem ipsum dolor sit amet, consectetur adipiscing elit. Morbi quis ante sed.</p>
    <a href="#">Read More</a>
  </div>
  <div class="abs svc" style="left:470px;top:743px">
    <div class="icon"><svg width="112" height="112" viewBox="0 0 112 112"><rect x="54" y="30" width="32" height="24" fill="none" stroke="#fff" stroke-width="3"/><rect x="66" y="54" width="6" height="8" fill="#fff"/><circle cx="40" cy="46" r="8" fill="#fff"/><path d="M30 58h20l10 14H48v14h-8V72H30z" fill="#fff"/><rect x="44" y="66" width="40" height="4" fill="#fff"/></svg></div>
    <h3>Online Coaching</h3>
    <p>Lorem ipsum dolor sit amet, consectetur adipiscing elit. Morbi quis ante sed.</p>
    <a href="#">Read More</a>
  </div>
  <div class="abs svc" style="left:804px;top:743px">
    <div class="icon"><svg width="112" height="112" viewBox="0 0 112 112"><g fill="#fff"><circle cx="34" cy="38" r="7"/><rect x="26" y="48" width="16" height="30" rx="3"/><circle cx="56" cy="34" r="8"/><rect x="47" y="45" width="18" height="36" rx="3"/><circle cx="78" cy="38" r="7"/><rect x="70" y="48" width="16" height="30" rx="3"/></g></svg></div>
    <h3>Outdoor Bootcamp</h3>
    <p>Lorem ipsum dolor sit amet, consectetur adipiscing elit. Morbi quis ante sed.</p>
    <a href="#">Read More</a>
  </div>
</section>

<section>
  <div class="abs about"></div>
  <div class="abs about-photo-bg" role="img" aria-label="Outdoor bootcamp group exercising on grass"></div>
  <h2 class="abs about-title">About Us</h2>
  <div class="abs rule" style="top:1155px;left:135px;width:578px;background:rgba(255,255,255,.25)"></div>
  <div class="abs" style="top:1153px;left:135px;width:78px;height:3px;background:var(--red)"></div>
  <div class="abs portrait" role="img" aria-label="Portrait of the trainer in a black t-shirt inside a gym"></div>
  <h3 class="abs about-head"><em>Motivation, Consistency</em> &amp; Intensity</h3>
  <p class="abs about-text">Lorem ipsum dolor sit amet, consectetur adipiscing elit. Sed vitae magna tellus. Aenean ante nunc, semper nec cursus non, rutrum ac eros. Vestibulum mattis justo ac dui bibendum consequat a ac ipsum. Praesent a arcu venenatis, auctor velit eu, suscipit libero. Quisque convallis, leo ac pharetra sagittis, ipsum arcu auctor urna, sit amet cursus risus augue in eros. Duis lacinia nisi vitae leo commodo, non finibus magna maximus. Sed posuere, neque eget bibendum pulvinar, ligula erat suscipit dolor, ut maximus arcu mi et tortor. Quisque imperdiet turpis et ligula mollis ultricies. Mauris lacinia rhoncus odio, at rutrum diam mollis eu.</p>
</section>

<section>
  <h2 class="abs sec-title reviews-title">CLIENT REVIEWS</h2>
  <div class="abs rule" style="top:1606px;left:132px;width:935px;background:#e3e3e3"></div>
  <div class="abs accent" style="top:1604px"></div>
  <div class="abs quote"><svg width="75" height="75" viewBox="0 0 75 75"><path d="M24 30h10v10l-5 8h-5l4-8h-4zM40 30h10v10l-5 8h-5l4-8h-4z" fill="#fff"/></svg></div>
  <p class="abs review">I have been training with Dario for just a few weeks now and am already feeling a difference between this and past efforts to get healthy. He's exactly what I was looking for- someone who has been where I am and knows what it's like to have to work hard to lose the weight and learn what it takes to get healthy. From his comprehensive initial assessment (and I mean comprehensive- you will work!) to a customized training plan (not off the shelf- it's what your specific body needs) and great group classes, Dario offers it all. I get both the 1:1 attention and the energy from being with other folks in a class.</p>
  <div class="abs stars">
    <svg width="20" height="20" viewBox="0 0 24 24"><path d="M12 2l3 7h7l-5.5 4.5 2 7.5L12 17l-6.5 4 2-7.5L2 9h7z" fill="#bbb"/></svg>
    <svg width="20" height="20" viewBox="0 0 24 24"><path d="M12 2l3 7h7l-5.5 4.5 2 7.5L12 17l-6.5 4 2-7.5L2 9h7z" fill="#bbb"/></svg>
    <svg width="20" height="20" viewBox="0 0 24 24"><path d="M12 2l3 7h7l-5.5 4.5 2 7.5L12 17l-6.5 4 2-7.5L2 9h7z" fill="#bbb"/></svg>
    <svg width="20" height="20" viewBox="0 0 24 24"><path d="M12 2l3 7h7l-5.5 4.5 2 7.5L12 17l-6.5 4 2-7.5L2 9h7z" fill="#bbb"/></svg>
    <svg width="20" height="20" viewBox="0 0 24 24"><path d="M12 2l3 7h7l-5.5 4.5 2 7.5L12 17l-6.5 4 2-7.5L2 9h7z" fill="#555"/></svg>
  </div>
  <p class="abs reviewer"><b>Tomas R. on</b> March 20, 2016</p>
</section>

<section>
  <div class="abs start"></div>
  <h2 class="abs sec-title" style="top:1874px;color:#fff">LET'S GET STARTED</h2>
  <div class="abs rule" style="top:1934px;left:132px;width:935px;background:#333"></div>
  <div class="abs accent" style="top:1932px"></div>
  <p class="abs thanks">Thank you for your interest in contacting VORELAN</p>
  <div class="abs info" style="left:228px;top:2014px">
    <span class="ring"><svg width="20" height="20" viewBox="0 0 20 20"><path d="M10 2a6 6 0 0 1 6 6c0 4-6 10-6 10S4 12 4 8a6 6 0 0 1 6-6z" fill="#fff"/><circle cx="10" cy="8" r="2.2" fill="#000"/></svg></span>
    <span>Lorem ipsum dolor sit<br>amet - 12345</span>
  </div>
  <div class="abs info" style="left:555px;top:2018px">
    <span class="ring"><svg width="20" height="20" viewBox="0 0 20 20"><path d="M5 3l3 3-2 2c1 2 3 4 5 5l2-2 3 3-2 2C9 16 4 11 4 5z" fill="#fff"/></svg></span>
    <span>012.555.0147</span>
  </div>
  <div class="abs info" style="left:783px;top:2018px">
    <span class="ring"><svg width="20" height="20" viewBox="0 0 20 20"><rect x="3" y="5" width="14" height="10" fill="#fff"/><path d="M3 5l7 6 7-6" stroke="#000" stroke-width="1.2" fill="none"/></svg></span>
    <span>info@vorelan.com</span>
  </div>
</section>

<section>
  <div class="abs form"></div>
  <div class="abs notch"></div>
  <h2 class="abs form-title">Please Fill Out The Form Below</h2>
  <div class="abs field" style="left:141px;top:2197px;width:294px;height:36px">Your Name</div>
  <div class="abs field" style="left:452px;top:2197px;width:294px;height:36px">Email</div>
  <div class="abs field" style="left:765px;top:2197px;width:294px;height:36px">Phone</div>
  <div class="abs field" style="left:141px;top:2244px;width:605px;height:74px">Comments</div>
  <div class="abs send">SEND</div>
</section>

<footer class="abs footer">
  <span class="copy">COPYRIGHT 2016 © VORELAN All Rights Reserved • Privacy Policy • Terms of Use</span>
  <div class="abs social"><span style="background:#bbb"></span><span style="background:#bbb"></span><span style="background:#bbb"></span><span style="background:#bbb"></span></div>
</footer>

</body>
</html>
```